High Tech Real Estate Startup needs a business card

We are developing an innovative real estate marketing product based around advanced search and virtual reality.

We talk to people, we need business cards.

Target Market(s)

The target market is technology professionals and realtors.

Contact Information for Business Card

The information to be included will include

Name
Title
Phone Number
E-mail Address
www.zelquin.com

It should use simple iconography for each one of those fields.

Font styles to use
Other font styles liked:
• Co, Jubilat, Avenir

Colors

Designer to choose colors to be used in the design.

Requirements
Must have
• Clean aesthetic,
• Good use of negative space.
• It should use our company logo, shown in the attached file. It is able to use the negative of that logo (coloured font and white background) and I have attached other acceptable accent colours in a swatch file.
Should not have
• Should not be too busy
• No extraneous text (slogans, tag lines etc)

```html
<!DOCTYPE html>
<html lang="en">
<head>
<meta charset="utf-8">
<title>Zelquin business card</title>
<link href="https://fonts.googleapis.com/css2?family=Montserrat:wght@400;500&display=swap" rel="stylesheet">
<style>
  :root {
    --bg: #ecebe8;
    --ink: #1f1f20;
    --card-dark: #252526;
    --teal: #17b3bd;
    --white: #ffffff;
    --muted: #8a8a8a;
  }
  * { margin: 0; padding: 0; box-sizing: border-box; }
  html, body { width: 1200px; height: 930px; overflow: hidden; background: var(--bg); }
  body { position: relative; font-family: "Montserrat", sans-serif; color: var(--ink); }

  .card {
    position: absolute;
    width: 580px; height: 330px;
    border-radius: 16px;
    overflow: hidden;
    box-shadow: 0 6px 18px rgba(0,0,0,0.18);
  }

  /* Back of card */
  .card-back { left: 60px; top: 90px; background: var(--card-dark); }
  .card-back .network {
    position: absolute; inset: 0;
    background: radial-gradient(ellipse at 55% 40%, #2d2d2e 0%, var(--card-dark) 70%);
  }
  .card-back .wordmark {
    position: absolute; left: 0; right: 0; top: 128px;
    text-align: center;
    font-size: 66px; font-weight: 500; letter-spacing: 2px;
    color: var(--teal);
  }

  /* Front of card */
  .card-front { left: 560px; top: 490px; background: var(--white); }
  .card-front .wordmark {
    position: absolute; left: 40px; top: 40px;
    font-size: 56px; font-weight: 500; letter-spacing: 1px;
    color: var(--teal);
  }
  .identity { position: absolute; right: 22px; top: 128px; text-align: right; }
  .identity .name { font-size: 20px; font-weight: 500; color: var(--teal); letter-spacing: 0.5px; line-height: 1.1; }
  .identity .title { font-size: 12px; color: var(--ink); margin-top: 2px; }
  .rule { position: absolute; left: 210px; right: 20px; top: 184px; height: 2px; background: var(--teal); }

  .contacts { position: absolute; left: 220px; top: 198px; list-style: none; }
  .contacts li { display: flex; align-items: center; gap: 8px; font-size: 14px; line-height: 20px; }
  .contacts svg { width: 11px; height: 11px; flex: none; }

  .address { position: absolute; right: 22px; top: 196px; text-align: right; font-size: 12.5px; line-height: 18px; }

  .base { position: absolute; left: 0; bottom: 0; width: 580px; height: 90px; }
</style>
</head>
<body>

<section class="card card-back">
  <div class="network" role="img" aria-label="Faint grey network of connected dots scattered across the dark card"></div>
  <div class="wordmark">ZELQUIN</div>
</section>

<section class="card card-front">
  <div class="wordmark">ZELQUIN</div>

  <div class="identity">
    <p class="name">DARREN HOLT</p>
    <p class="title">Director</p>
  </div>
  <div class="rule"></div>

  <ul class="contacts">
    <li>
      <svg viewBox="0 0 12 12"><path d="M3 1 L5 3.5 L4 5 C5 7 6 8 7.5 8.5 L9 7.5 L11 9.5 L9.5 11 C5 10.5 1.5 7 1 2.5 Z" fill="var(--teal)"/></svg>
      +1-555-014-2290
    </li>
    <li>
      <svg viewBox="0 0 12 12"><rect x="1" y="2.5" width="10" height="7" fill="none" stroke="var(--teal)" stroke-width="1.3"/><path d="M1 3 L6 7 L11 3" fill="none" stroke="var(--teal)" stroke-width="1.3"/></svg>
      info@zelquin.com
    </li>
    <li>
      <svg viewBox="0 0 12 12"><circle cx="6" cy="6" r="5" fill="none" stroke="var(--teal)" stroke-width="1.2"/><ellipse cx="6" cy="6" rx="2" ry="5" fill="none" stroke="var(--teal)" stroke-width="1"/><path d="M1 6 H11" stroke="var(--teal)" stroke-width="1"/></svg>
      www.zelquin.com
    </li>
  </ul>

  <div class="address">
    <p>73 Larkspur Ridge Rd.</p>
    <p>Fairview, OR 97024</p>
  </div>

  <svg class="base" viewBox="0 0 580 90" preserveAspectRatio="none">
    <path d="M0 80 L340 80 C375 80 380 30 420 28 L580 28 L580 90 L0 90 Z" fill="var(--card-dark)"/>
    <path d="M0 73 L330 73 C350 73 360 60 368 46" fill="none" stroke="var(--teal)" stroke-width="4"/>
  </svg>
</section>

</body>
</html>
```